Corporate Travel Technology Company needs new Business Card design

We need a new business card design to reflect our re-branded company. Our company is called tolvEn (pronounced tolvenn) and we provide Business Intelligence and mobile travel management solutions for the corporate travel industry. Our multinational customers use our solutions to manage large travel budgets and frequent travellers, as well as to save money and reduce risk. We'd like to see designs that use the blue and green palette as well as our corporate logo (attached below). The design should communicate innovation, insight, forward thinking, contemporary, trusted.

Target Market(s)

Large multinational corporates and Travel Agencies.

Industry/Entity Type

Business

Contact Information for Business Card

Rosalind Mercer
Chief Executive
tolvEn
Phone number - +61 (0)2 8134 2907
Email address - rosalind.mercer@tolven-example.com
Mobile number - +61 (0)438 516 702
www.tolven-example.com

Font styles to use
Other font styles liked:
• Please use font as close to corporate logo as possible

Colors
0255a3
0393ce
00a990
33b8a4
33a6d7
3176b5

Requirements
Must have
• Please include the words;
• Mobile Travel Management
• Accelerating Travel Business Insights
• Use corporate logo - although icon can be stylised if needed

```html
<!DOCTYPE html>
<html lang="en">
<head>
<meta charset="utf-8">
<title>TOLVEN business card</title>
<link href="https://fonts.googleapis.com/css2?family=Montserrat:wght@400;600;700&family=Quicksand:wght@400;500&display=swap" rel="stylesheet">
<style>
  :root {
    --page: #e9ecef;
    --ink-dark: #1b2325;
    --ink-dark-2: #2d3a3d;
    --brand-blue: #0393ce;
    --brand-sky: #33a6d7;
    --brand-deep: #0255a3;
    --paper: #ffffff;
    --soft-text: #d3dadc;
  }
  * { box-sizing: border-box; margin: 0; padding: 0; }
  html, body { width: 1200px; height: 913px; overflow: hidden; }
  body {
    background: var(--page);
    display: flex;
    align-items: center;
    justify-content: center;
    gap: 60px;
    font-family: "Quicksand", sans-serif;
  }
  .card {
    position: relative;
    width: 520px;
    height: 298px;
    border-radius: 16px;
    overflow: hidden;
    box-shadow: 0 6px 18px rgba(0,0,0,0.18);
  }
  .card-front { background: var(--paper); }
  .front-shape { position: absolute; inset: 0; width: 100%; height: 100%; }
  .wordmark {
    position: absolute;
    top: 44px;
    right: 40px;
    font-family: "Montserrat", sans-serif;
    font-weight: 600;
    font-size: 40px;
    letter-spacing: 6px;
    color: var(--brand-deep);
    line-height: 1;
  }
  .holder {
    position: absolute;
    left: 32px;
    top: 176px;
  }
  .holder-name {
    font-family: "Montserrat", sans-serif;
    font-weight: 700;
    font-size: 17px;
    letter-spacing: 0.5px;
    color: var(--brand-blue);
    text-transform: uppercase;
  }
  .holder-role {
    font-family: "Montserrat", sans-serif;
    font-size: 11.5px;
    color: var(--soft-text);
    margin-top: 2px;
  }
  .contact-list {
    list-style: none;
    margin-top: 8px;
    font-size: 11px;
    color: var(--brand-sky);
    line-height: 16px;
  }
  .contact-list li { display: flex; align-items: center; gap: 8px; }
  .contact-list svg { width: 10px; height: 10px; flex: none; }
  .card-back {
    background: linear-gradient(160deg, #5ccaf0 0%, var(--brand-sky) 45%, #1b7fcf 100%);
  }
  .back-accent {
    position: absolute;
    left: -40px;
    top: 60px;
    width: 200px;
    height: 260px;
    border-radius: 50%;
    background: rgba(255,255,255,0.08);
  }
  .taglines {
    position: absolute;
    right: 34px;
    bottom: 40px;
    list-style: none;
    font-family: "Montserrat", sans-serif;
    font-weight: 600;
    font-size: 15px;
    color: var(--paper);
    text-align: right;
    line-height: 22px;
  }
  .taglines li { display: flex; align-items: center; justify-content: flex-end; gap: 8px; }
  .bullet {
    width: 10px; height: 10px;
    border: 1.5px solid var(--paper);
    border-radius: 50%;
  }
</style>
</head>
<body>
  <section class="card card-front" aria-label="Business card front">
    <svg class="front-shape" viewBox="0 0 520 298" preserveAspectRatio="none" aria-hidden="true">
      <defs>
        <linearGradient id="darkPanel" x1="0" y1="0" x2="0" y2="1">
          <stop offset="0" stop-color="#2d3a3d"/>
          <stop offset="1" stop-color="#1b2325"/>
        </linearGradient>
      </defs>
      <path d="M0 118 C150 150 330 200 520 205 L520 298 L0 298 Z" fill="url(#darkPanel)"/>
      <path d="M0 110 C150 142 330 192 520 197" fill="none" stroke="#0393ce" stroke-width="3"/>
    </svg>
    <div class="wordmark">TOLVEN</div>
    <div class="holder">
      <p class="holder-name">Rosalind Mercer</p>
      <p class="holder-role">Chief Executive</p>
      <ul class="contact-list">
        <li><svg viewBox="0 0 10 10"><rect x="2.5" y="0.5" width="5" height="9" rx="1" fill="none" stroke="#d3dadc"/></svg>+61 (0)438 516 702</li>
        <li><svg viewBox="0 0 10 10"><path d="M2 1 L4 1 L5 3.5 L3.8 4.5 C4.5 6 5.5 7 6.5 7.5 L7.5 6.3 L9.5 7.5 L9.5 9 C5 9.5 0.5 5 1 1 Z" fill="#d3dadc"/></svg>+61 (0)2 8134 2907</li>
        <li><svg viewBox="0 0 10 10"><circle cx="5" cy="5" r="4" fill="none" stroke="#d3dadc"/><path d="M1 5 H9 M5 1 C3 3.5 3 6.5 5 9 C7 6.5 7 3.5 5 1" fill="none" stroke="#d3dadc" stroke-width="0.8"/></svg>www.tolven-example.com</li>
        <li><svg viewBox="0 0 10 10"><rect x="0.5" y="2" width="9" height="6" fill="none" stroke="#d3dadc"/><path d="M0.5 2 L5 5.5 L9.5 2" fill="none" stroke="#d3dadc"/></svg>rosalind.mercer@tolven-example.com</li>
      </ul>
    </div>
  </section>

  <section class="card card-back" aria-label="Business card back">
    <div class="back-accent"></div>
    <ul class="taglines">
      <li><span class="bullet"></span>Accelerating Travel Business Insights</li>
      <li><span class="bullet"></span>Mobile Travel Management</li>
    </ul>
  </section>
</body>
</html>
```